Business Card Design Competition

We need a business card design for our Internet Marketing company. We require both front and back designs and the final card must be 89x53mm in size, plus crop marks to 91x55mm. Colours as per logo, plus perhaps black and/or grey (#828282).
Final text must be editable (if you can supply an editable Fireworks PNG, even better)...
FRONT TEXT:
Full Name
Position
Address Line
Suburb, State, Postcode
Phone: 0000 000 000
Mobile: 0000 000 000
Email: xxx@brightlanemedia.com.au
Web: www.brightlanemedia.com.au
Rear of card should be a fresh design plus our slogan text: "Getting You Noticed" in large font, then in small text "Kestrel Holdings Pty Ltd (ABN: 42 561 903 774)".
Target Market(s)
Small/Medium Businesses
Industry/Entity Type
Business

```html
<!DOCTYPE html>
<html lang="en">
<head>
<meta charset="utf-8">
<title>Brightlane Media – Business Card, Front and Back</title>
<link rel="stylesheet" href="https://fonts.googleapis.com/css2?family=Arimo:wght@400;700&display=swap">
<style>
  :root {
    --green: #8cc63f;
    --grey: #828282;
    --black: #000000;
    --white: #ffffff;
    --orange: #f7941d;
    --ink: #111111;
    --edge: #d9d9d9;
  }
  * { box-sizing: border-box; margin: 0; padding: 0; }
  html, body {
    width: 1200px;
    height: 371px;
    overflow: hidden;
    background: var(--white);
    font-family: "Arimo", Arial, sans-serif;
  }
  .canvas {
    position: relative;
    width: 1200px;
    height: 371px;
  }
  .card {
    position: absolute;
    top: 7px;
    width: 578px;
    height: 349px;
    background: var(--green);
    overflow: hidden;
    outline: 1px solid var(--edge);
  }
  .card--front { left: 9px; }
  .card--back { left: 606px; }

  /* Brand lockup: plain circle + name */
  .brand {
    position: absolute;
    display: flex;
    align-items: center;
    gap: 10px;
  }
  .brand__dot {
    width: 44px;
    height: 44px;
    border-radius: 50%;
    background: var(--orange);
    flex: none;
  }
  .brand__name {
    font-weight: 700;
    font-size: 27px;
    line-height: 1;
    color: var(--green);
    white-space: nowrap;
  }

  /* Front */
  .front__header {
    position: absolute;
    left: 0; top: 0;
    width: 100%;
    height: 98px;
    background: var(--white);
  }
  .front__header .brand { left: 14px; top: 26px; }
  .front__nameband {
    position: absolute;
    left: 0; top: 98px;
    width: 100%;
    height: 46px;
    background: var(--grey);
  }
  .front__name {
    position: absolute;
    left: 268px;
    top: 11px;
    font-size: 22px;
    color: var(--ink);
  }
  .contact {
    position: absolute;
    left: 258px;
    top: 188px;
    list-style: none;
    font-size: 14px;
    line-height: 17px;
    color: var(--ink);
  }

  /* Back */
  .back__logoband {
    position: absolute;
    left: 0; top: 104px;
    width: 100%;
    height: 94px;
    background: var(--black);
  }
  .back__logoband .brand {
    left: 50%;
    top: 25px;
    transform: translateX(-50%);
  }
  .back__sloganband {
    position: absolute;
    left: 0; top: 198px;
    width: 100%;
    height: 44px;
    background: var(--grey);
    display: flex;
    align-items: center;
    justify-content: center;
  }
  .slogan {
    font-size: 27px;
    color: var(--ink);
  }
</style>
</head>
<body>
<main class="canvas">

  <section class="card card--front" aria-label="Business card front">
    <header class="front__header">
      <div class="brand">
        <span class="brand__dot"></span>
        <span class="brand__name">Brightlane Media</span>
      </div>
    </header>
    <div class="front__nameband">
      <p class="front__name">Sample Name</p>
    </div>
    <ul class="contact">
      <li>Adress line</li>
      <li>Subrb, State, postcode</li>
      <li>Phone: 0000 000 000</li>
      <li>mobile: 0000 000 000</li>
      <li>Email: xxx@brightlanemedia.com.au</li>
      <li>Web: www.brightlanemedia.com.au</li>
    </ul>
  </section>

  <section class="card card--back" aria-label="Business card back">
    <div class="back__logoband">
      <div class="brand">
        <span class="brand__dot"></span>
        <span class="brand__name">Brightlane Media</span>
      </div>
    </div>
    <div class="back__sloganband">
      <p class="slogan">Getting You Noticed</p>
    </div>
  </section>

</main>
</body>
</html>
```